Hello my Name is Elias Moreno. I buy and sell vintage comic books, you can refer to my instragram page qpkz.comics to get ideas and inspiration. For the front of the card I would like my company logo QPKZ Comics with a yellow and black background with the bat signal or bat emblem like on my IG page and with my info Elias Moreno as the Owner and address/ phone number, PO Box 617283, Miami, FL 33827, 305-482-6170 and that I buy and sell comics & collectables . Also feel free to be open to other ideas if you want. Im not stuck on one design. For the back of the card I would like for it to say follow me on Instagram QPKZ.Comics with the ig emblem. Also would like the card to be vertical if possible. Thanks

```html
<!DOCTYPE html>
<html lang="en">
<head>
<meta charset="utf-8">
<title>QPKZ Comics – Business Card</title>
<link rel="stylesheet" href="https://fonts.googleapis.com/css2?family=Source+Sans+3:wght@400;600;700&display=swap">
<style>
  :root {
    --backdrop: #dadada;
    --ink: #000000;
    --gold: #fbc918;
    --paper-text: #ffffff;
    --dark-text: #1a1a1a;
  }
  * { margin: 0; padding: 0; box-sizing: border-box; }
  html, body {
    width: 1200px; height: 900px; overflow: hidden;
    background: var(--backdrop);
    font-family: "Source Sans 3", "Myriad Pro", Arial, sans-serif;
  }
  .canvas { position: relative; width: 1200px; height: 900px; }

  .card { position: absolute; top: 200px; width: 310px; height: 502px; overflow: hidden; }

  /* Front */
  .card-front { left: 265px; background: var(--ink); }
  .brand-name {
    position: absolute; left: 80px; width: 200px; top: 94px;
    text-align: center; color: var(--gold);
    font-weight: 700; font-size: 34px; letter-spacing: 1px; line-height: 1;
    white-space: nowrap;
  }
  .contact { position: absolute; left: 39px; top: 319px; color: var(--paper-text); }
  .contact-name { color: var(--gold); font-weight: 600; font-size: 19px; line-height: 24px; }
  .contact-role { font-size: 14px; line-height: 18px; }
  .contact-phone { margin-top: 20px; font-size: 14.5px; line-height: 18px; display: flex; align-items: center; gap: 2px; }
  .contact-phone svg { width: 11px; height: 11px; fill: var(--gold); }
  .contact-address { margin-top: 14px; font-size: 14.5px; line-height: 21px; }

  /* Back */
  .card-back { left: 641px; background: var(--gold); }
  .follow {
    position: absolute; top: 14px; left: 0; width: 100%;
    display: flex; justify-content: center; align-items: center; gap: 7px;
    color: var(--dark-text); font-weight: 600;
  }
  .follow-label { font-size: 14.5px; margin-left: 28px; }
  .follow-mark { width: 18px; height: 18px; background: var(--dark-text); border-radius: 3px; }
  .follow-handle { font-size: 13.5px; }
  .emblem-area { position: absolute; left: 0; top: 44px; width: 293px; height: 458px; }
  .tagline {
    position: absolute; left: 31px; top: 148px;
    color: var(--gold); font-weight: 600; line-height: 1;
    white-space: nowrap;
  }
  .tagline span { display: block; }
  .tagline-lead { font-size: 59px; margin-bottom: 4px; }
  .tagline-mid { font-size: 46px; margin-bottom: 4px; }
  .tagline-end { font-size: 30px; }
</style>
</head>
<body>
<main class="canvas">
  <section class="card card-front" aria-label="Card front">
    <div class="brand-name">QPKZ COMICS</div>
    <div class="contact">
      <p class="contact-name">Elias Moreno</p>
      <p class="contact-role">Owner</p>
      <p class="contact-phone">
        <svg viewBox="0 0 24 24" aria-hidden="true"><path d="M6.6 10.8a15.1 15.1 0 0 0 6.6 6.6l2.2-2.2a1 1 0 0 1 1-.25 11.4 11.4 0 0 0 3.6.57 1 1 0 0 1 1 1V20a1 1 0 0 1-1 1A17 17 0 0 1 3 4a1 1 0 0 1 1-1h3.5a1 1 0 0 1 1 1c0 1.25.2 2.45.57 3.570a1 1 0 0 1-.25 1z"/></svg>
        305-482-6170
      </p>
      <p class="contact-address">PO Box 617283<br>Miami, FL 33827</p>
    </div>
  </section>

  <section class="card card-back" aria-label="Card back">
    <div class="follow">
      <span class="follow-label">Follow me on</span>
      <span class="follow-mark" aria-hidden="true"></span>
      <span class="follow-handle">QPKZ.Comics</span>
    </div>
    <svg class="emblem-area" viewBox="0 0 293 458" role="img" aria-label="Large dark emblem decoration area">
      <rect width="293" height="458" fill="var(--ink)"/>
    </svg>
    <h1 class="tagline">
      <span class="tagline-lead">WE BUY</span>
      <span class="tagline-mid">AND SELL</span>
      <span class="tagline-mid">COMICS &amp;</span>
      <span class="tagline-end">COLLECTABLES</span>
    </h1>
  </section>
</main>
</body>
</html>
```